Website for steady harbor detailing.

Need a homepage, pages for: car and truck detailing, boat detailing, airplane detailing, about us, contact us. I have the domain name through nimbushelm so I will need the design uploaded on my domain. Also hoping to link other domains to this page.I would like to see the logo more pronounced. I would like to see a large phone number link to call my business. The layout looks nice but the pics need to depict car washing and waxing not car mechanics. i would like the colors of the webpage to incorporate the colors found in the logo in some way. I would like links to social media pages
Updates

Target Market(s)

Local customers in Vero Beach, Florida.

Number of Pages Required

5+ page

Colors

Requirements
Must have
• Easy to navigate, attractive pages with pictures and logo, professional looking. must have my phone number and logo very prevalent and links to call or go to home page. I would like links to my social media accounts on the home page.
Nice to have
• Easy to navigate, attractive pages with pictures and logo, professional looking.

```html
<!DOCTYPE html>
<html lang="en">
<head>
<meta charset="utf-8">
<title>Steady Harbor Detailing</title>
<link rel="stylesheet" href="https://fonts.googleapis.com/css2?family=Lato:ital,wght@0,400;0,700;0,900;1,400&display=swap">
<style>
:root{
  --navy:#1f1b7c;
  --red:#d8141c;
  --blue:#1b8fe3;
  --sky:#1c80d2;
  --ink:#222;
  --muted:#666;
  --line:#d9d9d9;
  --lavender:#eeeefb;
}
*{box-sizing:border-box;margin:0;padding:0}
a{text-decoration:none;color:inherit}
html,body{width:1200px;height:3422px;overflow:hidden}
body{position:relative;font-family:'Lato',sans-serif;color:var(--ink);background:#fff}

/* header */
.site-header{position:absolute;left:0;top:0;width:1200px;height:100px;background:#fff}
.brand{position:absolute;left:98px;top:18px;display:flex;align-items:center;gap:12px}
.brand-mark{width:54px;height:54px;border-radius:50%;background:var(--navy)}
.brand-name{font-weight:900;font-size:24px;color:var(--navy);line-height:1}
.header-call{position:absolute;right:98px;top:12px;display:flex;align-items:center;gap:10px;font-size:20px;color:var(--navy);font-weight:700}
.header-call .lbl{font-weight:400;color:var(--ink);font-size:18px}
.call-ring{width:34px;height:34px;border:2px solid var(--red);border-radius:50%;display:flex;align-items:center;justify-content:center}
.main-nav{position:absolute;right:98px;top:64px;display:flex;gap:22px;font-size:17px;font-weight:700;color:#222}
.main-nav .active{color:var(--red)}

/* hero */
.hero{position:absolute;left:0;top:100px;width:1200px;height:555px;overflow:hidden}
.hero-photo{position:absolute;inset:0;background:linear-gradient(110deg,#3a3f46 0%,#8b9097 35%,#5b6068 60%,#262a30 100%)}
.hero h1{position:absolute;top:150px;width:100%;text-align:center;color:#fff;font-size:50px;font-weight:900;letter-spacing:.5px}
.hero .sub{position:absolute;top:226px;width:100%;text-align:center;color:#fff;font-size:28px}
.btn{display:inline-block;background:var(--red);color:#fff;font-weight:700;text-transform:uppercase;border-radius:30px;text-align:center}
.hero .btn{position:absolute;left:462px;top:282px;width:276px;height:56px;line-height:56px;font-size:16px}
.hero-dots{position:absolute;top:473px;left:568px;display:flex;gap:5px}
.hero-dots span{width:13px;height:13px;border-radius:50%;border:2px solid #fff}
.hero-dots span.on{background:#fff}
.hero-curve{position:absolute;left:0;top:0}

/* section titles */
.section-title{position:absolute;width:1200px;text-align:center;color:var(--navy);font-size:31px;font-weight:900}

/* welcome */
.intro{position:absolute;top:786px;width:1200px;text-align:center;font-size:16px;color:var(--muted);line-height:28px}
.big-call{position:absolute;top:857px;width:1200px;text-align:center;font-size:27px;color:var(--ink)}
.big-call b{color:var(--red);font-weight:900}
.feature{position:absolute;top:935px;width:260px;text-align:center}
.feature .ring{width:160px;height:160px;border:1.5px solid #888;border-radius:50%;margin:0 auto;display:flex;align-items:center;justify-content:center}
.feature h3{margin-top:30px;font-size:19px;font-weight:700}
.feature p{margin-top:12px;font-size:14px;color:var(--muted);line-height:24px}

/* services */
.services{position:absolute;left:0;top:1277px;width:1200px;height:636px;background:var(--lavender)}
.tabs{position:absolute;top:1403px;width:1200px;display:flex;justify-content:center;gap:60px;font-size:17px;font-weight:700}
.tabs .on{color:var(--blue);text-decoration:underline}
.service-card{position:absolute;top:1467px;width:313px;height:377px;background:#fff;border:1px solid #dcdcdc;box-shadow:0 2px 6px rgba(0,0,0,.08);text-align:center}
.service-photo{margin:4px;height:172px}
.service-card h3{margin-top:34px;font-size:22px;font-weight:900}
.service-card p{margin:14px 26px 0;font-size:14px;line-height:23px;color:var(--muted)}
.service-card .more{display:block;margin-top:18px;color:var(--red);font-size:14px;font-weight:900}

/* why */
.why-title{position:absolute;left:98px;top:1990px;color:var(--navy);font-size:31px;font-weight:900;line-height:48px}
.why-text{position:absolute;left:98px;top:2106px;width:520px;font-size:15px;color:var(--muted);line-height:25px}
.ticks{position:absolute;left:98px;top:2180px;list-style:none;font-size:15px;color:var(--muted)}
.ticks li{display:flex;align-items:center;gap:14px;height:30px}
.why-btn{position:absolute;left:98px;top:2326px;width:136px;height:48px;line-height:48px;font-size:15px}
.why-photo{position:absolute;left:650px;top:1998px;width:450px;height:381px;border:6px solid #fff;box-shadow:0 0 0 1px #ccc}

/* testimonials */
.testimonials{position:absolute;left:0;top:2468px;width:1200px;height:468px;background:linear-gradient(180deg,#2a8fdc,#1570c4)}
.testimonials .section-title{color:#fff;top:54px}
.quote-card{position:absolute;top:173px;width:308px;height:229px;border:2px solid rgba(255,255,255,.85);border-radius:6px;text-align:center;color:#fff}
.avatar{position:absolute;left:112px;top:-44px;width:84px;height:84px;border-radius:50%;border:3px solid #fff;background:linear-gradient(180deg,#c9b39e,#8a6f5a)}
.quote-card p{margin:62px 26px 0;font-style:italic;font-size:13.5px;line-height:22px}
.quote-card h4{margin-top:14px;font-size:18px;font-weight:700}
.arrow{position:absolute;top:300px;width:36px;height:36px;border-radius:50%;background:rgba(255,255,255,.9);display:flex;align-items:center;justify-content:center}

/* contact */
.block-title{position:absolute;color:var(--navy);font-size:21px;font-weight:900}
.field{position:absolute;height:34px;border:1px solid #bbb;font-size:12px;color:#444;padding:9px 14px}
.submit{position:absolute;left:630px;top:3272px;width:96px;height:36px;line-height:36px;font-size:14px}
.info{position:absolute;left:782px;display:flex;gap:20px;font-size:14px;color:#444;line-height:22px}
.info .ic{width:34px;height:34px;border:1.5px solid var(--blue);border-radius:50%;display:flex;align-items:center;justify-content:center;flex:none}
.socials{position:absolute;left:782px;top:3274px;display:flex;gap:10px}
.socials span{width:34px;height:34px;border:1.5px solid var(--blue);border-radius:50%}
.footer-line{position:absolute;left:98px;top:3342px;width:1004px;border-top:1px solid var(--line)}
.copyright{position:absolute;top:3372px;width:1200px;text-align:center;font-size:13px;color:#444}
.to-top{position:absolute;left:1070px;top:3374px}
</style>
</head>
<body>

<header class="site-header">
  <a class="brand" href="#"><span class="brand-mark"></span><span class="brand-name">Steady Harbor Detailing</span></a>
  <div class="header-call">
    <span class="call-ring"><svg width="16" height="16" viewBox="0 0 24 24"><path fill="#d8141c" d="M6.6 10.8a15 15 0 0 0 6.6 6.6l2.2-2.2c.3-.3.7-.4 1-.2 1.1.4 2.3.6 3.6.6.6 0 1 .4 1 1V20c0 .6-.4 1-1 1C10.6 21 3 13.4 3 4c0-.6.4-1 1-1h3.5c.6 0 1 .4 1 1 0 1.3.2 2.5.6 3.6.1.3 0 .7-.2 1z"/></svg></span>
    <span class="lbl">Call us on:</span> 555-210-4387
  </div>
  <nav class="main-nav">
    <span class="active">Home</span><span>About</span><span>Cars</span><span>Boats</span><span>Airplanes</span><span>Services</span><span>News</span><span>Contact</span>
    <svg width="18" height="18" viewBox="0 0 24 24"><circle cx="10" cy="10" r="6.5" fill="none" stroke="#222" stroke-width="3"/><path d="M15 15l6 6" stroke="#222" stroke-width="3"/></svg>
  </nav>
</header>

<section class="hero">
  <div class="hero-photo" role="img" aria-label="Detailer polishing the side of a dark car"></div>
  <h1>STEADY HARBOR DETAILING</h1>
  <div class="sub">Cars, Boats, and Airplanes</div>
  <a class="btn" href="#">Book Your Appointment</a>
  <div class="hero-dots"><span class="on"></span><span></span><span></span><span></span></div>
  <svg class="hero-curve" width="1200" height="555" viewBox="0 0 1200 555">
    <path d="M0 420 Q600 640 1200 420 L1200 555 L0 555 Z" fill="#fff"/>
    <path d="M0 420 Q600 640 1200 420 L1200 445 Q600 655 0 445 Z" fill="#1f1b7c"/>
  </svg>
</section>

<h2 class="section-title" style="top:724px">WELCOME TO STEADY HARBOR DETAILING</h2>
<p class="intro">We are the top rated pool repair company in harbor bay county and pride ourselves on customer satisfaction.<br>Our main business is detailing cars, boats, and airplanes. Wash, wax, degrease, we do it all.</p>
<p class="big-call"><svg width="22" height="22" viewBox="0 0 24 24" style="vertical-align:-2px"><path fill="#333" d="M6.6 10.8a15 15 0 0 0 6.6 6.6l2.2-2.2c.3-.3.7-.4 1-.2 1.1.4 2.3.6 3.6.6.6 0 1 .4 1 1V20c0 .6-.4 1-1 1C10.6 21 3 13.4 3 4c0-.6.4-1 1-1h3.5c.6 0 1 .4 1 1 0 1.3.2 2.5.6 3.6.1.3 0 .7-.2 1z"/></svg> Call us on : <b>555-210-4387</b></p>

<div class="feature" style="left:78px">
  <div class="ring"><svg width="64" height="56" viewBox="0 0 64 56"><circle cx="32" cy="14" r="10" fill="#1b8fe3"/><path d="M16 50c0-12 7-20 16-20s16 8 16 20z" fill="#1b8fe3"/><circle cx="12" cy="20" r="7" fill="#1b8fe3"/><circle cx="52" cy="20" r="7" fill="#1b8fe3"/><path d="M0 46c0-9 5-15 12-15 3 0 5 1 7 3-3 4-5 8-5 12z M64 46c0-9-5-15-12-15-3 0-5 1-7 3 3 4 5 8 5 12z" fill="#1b8fe3"/></svg></div>
  <h3>Customer Satisfaction</h3><p>Omnis dolor repellendu mporib us<br>autem qrum neuibus da</p>
</div>
<div class="feature" style="left:340px">
  <div class="ring"><svg width="58" height="56" viewBox="0 0 24 23"><path fill="#1b8fe3" d="M12 0l3.1 7.6 8.2.7-6.2 5.4 1.9 8-7-4.3-7 4.3 1.9-8L.7 8.3l8.2-.7z"/></svg></div>
  <h3>Top Rated</h3><p>Omnis dolor repellendu mporib us<br>autem qrum neuibus da</p>
</div>
<div class="feature" style="left:600px">
  <div class="ring"><svg width="56" height="56" viewBox="0 0 56 56"><path fill="#1b8fe3" d="M28 2l6 6 8-2 2 8 8 2-2 8 6 6-6 6 2 8-8 2-2 8-8-2-6 6-6-6-8 2-2-8-8-2 2-8-6-6 6-6-2-8 8-2 2-8 8 2z"/></svg></div>
  <h3>High Quality</h3><p>Omnis dolor repellendu mporib us<br>autem qrum neuibus da</p>
</div>
<div class="feature" style="left:860px">
  <div class="ring"><svg width="58" height="56" viewBox="0 0 58 56"><rect x="2" y="24" width="12" height="30" rx="2" fill="#1b8fe3"/><path fill="#1b8fe3" d="M18 26l12-20c3-4 9-2 8 3l-3 13h16c4 0 6 3 5 6l-5 22c-1 3-3 4-6 4H18z"/></svg></div>
  <h3>Best Experience</h3><p>Omnis dolor repellendu mporib us<br>autem qrum neuibus da</p>
</div>

<section class="services"></section>
<h2 class="section-title" style="top:1340px">OUR SERVICES</h2>
<div class="tabs"><span class="on">CAR</span><span>BOATS</span><span>AIRPLANES</span></div>

<article class="service-card" style="left:98px">
  <div class="service-photo" role="img" aria-label="Car wheel being washed with foam spray" style="background:linear-gradient(135deg,#d9dde1,#7b8087 60%,#3b3f45)"></div>
  <h3>WASH</h3><p>Nam libero tempore, cum soluta nobis est eligendi optio cumque nihil impedi quo minus id quod maxime placeat</p><span class="more">READ MORE</span>
</article>
<article class="service-card" style="left:443px">
  <div class="service-photo" role="img" aria-label="Gloved hand waxing a red car panel with a polisher" style="background:linear-gradient(135deg,#c5c9cd,#b8242b 55%,#5a1417)"></div>
  <h3>WAX</h3><p>Nam libero tempore, cum soluta nobis est eligendi optio cumque nihil impedi quo minus id quod maxime placeat</p><span class="more">READ MORE</span>
</article>
<article class="service-card" style="left:787px">
  <div class="service-photo" role="img" aria-label="Gloved hand spraying cleaner on a car dashboard" style="background:linear-gradient(135deg,#3c3f44,#d9c04a 55%,#e7d86a)"></div>
  <h3>DEGREASE</h3><p>Nam libero tempore, cum soluta nobis est eligendi optio cumque nihil impedi quo minus id quod maxime placeat</p><span class="more">READ MORE</span>
</article>

<h2 class="why-title">WHY DETAILING WITH<br>STEADY HARBOR DETAILING?</h2>
<p class="why-text">At vero eos et accusamus et iusto odio dignissimos ducimus qui blanditiis prae sentium voluptatum deleniti atque corrup.</p>
<ul class="ticks">
  <li><svg width="16" height="16" viewBox="0 0 16 16"><circle cx="8" cy="8" r="8" fill="#1b8fe3"/><path d="M4 8l3 3 5-6" stroke="#fff" stroke-width="2" fill="none"/></svg>Nam libero tempore, cum soluta nobis est eligendi optio cumque nih</li>
  <li><svg width="16" height="16" viewBox="0 0 16 16"><circle cx="8" cy="8" r="8" fill="#1b8fe3"/><path d="M4 8l3 3 5-6" stroke="#fff" stroke-width="2" fill="none"/></svg>Impedit quo minus id quod maxime placeat facere possimus, omni</li>
  <li><svg width="16" height="16" viewBox="0 0 16 16"><circle cx="8" cy="8" r="8" fill="#1b8fe3"/><path d="M4 8l3 3 5-6" stroke="#fff" stroke-width="2" fill="none"/></svg>Voluptas assumenda est, omnis dolor repellendu mporibus autem</li>
  <li><svg width="16" height="16" viewBox="0 0 16 16"><circle cx="8" cy="8" r="8" fill="#1b8fe3"/><path d="M4 8l3 3 5-6" stroke="#fff" stroke-width="2" fill="none"/></svg>Tuibusdam et aut officiis debitis aut rerum necessitatibus saepe eve</li>
</ul>
<a class="btn why-btn" href="#">Read More</a>
<div class="why-photo" role="img" aria-label="Soapy car wheel beside a red bucket and sponges" style="background:linear-gradient(160deg,#50565c,#9aa1a8 50%,#c34a3a 80%,#c8ccd0)"></div>

<section class="testimonials">
  <h2 class="section-title">CLIENT TESTIMONIALS</h2>
  <div class="arrow" style="left:30px"><svg width="14" height="14" viewBox="0 0 14 14"><path d="M9 2L4 7l5 5" stroke="#1570c4" stroke-width="2.5" fill="none"/></svg></div>
  <div class="quote-card" style="left:98px"><div class="avatar" role="img" aria-label="Client portrait"></div><p>Nam libero tempore, cum soluta nobis est eligendi optio cumque nihil impedit quo minus id quod maxime placeat facere possi mus, omnis voluptas assumend</p><h4>Nora Whitfield</h4></div>
  <div class="quote-card" style="left:446px"><div class="avatar" role="img" aria-label="Client portrait"></div><p>Nam libero tempore, cum soluta nobis est eligendi optio cumque nihil impedit quo minus id quod maxime placeat facere possi mus, omnis voluptas assumend</p><h4>Tessa Brandt</h4></div>
  <div class="quote-card" style="left:794px"><div class="avatar" role="img" aria-label="Client portrait"></div><p>Nam libero tempore, cum soluta nobis est eligendi optio cumque nihil impedit quo minus id quod maxime placeat facere possi mus, omnis voluptas assumend</p><h4>Owen Marsh</h4></div>
  <div class="arrow" style="left:1134px"><svg width="14" height="14" viewBox="0 0 14 14"><path d="M5 2l5 5-5 5" stroke="#1570c4" stroke-width="2.5" fill="none"/></svg></div>
</section>

<h3 class="block-title" style="left:98px;top:3014px">CONTACT FORM</h3>
<div class="field" style="left:98px;top:3081px;width:308px">First Name</div>
<div class="field" style="left:418px;top:3081px;width:308px">Last Name</div>
<div class="field" style="left:98px;top:3126px;width:308px">Email Address *</div>
<div class="field" style="left:418px;top:3126px;width:308px">Subject *</div>
<div class="field" style="left:98px;top:3172px;width:628px;height:82px">Message *</div>
<a class="btn submit" href="#">Submit</a>

<h3 class="block-title" style="left:782px;top:3014px">CONTACT INFORMATION</h3>
<div class="info" style="top:3060px"><span class="ic"><svg width="14" height="16" viewBox="0 0 14 18"><path fill="#1b8fe3" d="M7 0a7 7 0 0 0-7 7c0 5 7 11 7 11s7-6 7-11a7 7 0 0 0-7-7zm0 9.5A2.5 2.5 0 1 1 7 4.5a2.5 2.5 0 0 1 0 5z"/></svg></span><span>4120 Harbor Point Road,<br>Suite #B-12,</span></div>
<div class="info" style="top:3120px;line-height:34px"><span class="ic"><svg width="14" height="14" viewBox="0 0 24 24"><path fill="#1b8fe3" d="M6.6 10.8a15 15 0 0 0 6.6 6.6l2.2-2.2c.3-.3.7-.4 1-.2 1.1.4 2.3.6 3.6.6.6 0 1 .4 1 1V20c0 .6-.4 1-1 1C10.6 21 3 13.4 3 4c0-.6.4-1 1-1h3.5c.6 0 1 .4 1 1 0 1.3.2 2.5.6 3.6.1.3 0 .7-.2 1z"/></svg></span><span>555-210-4387</span></div>
<div class="info" style="top:3170px;line-height:34px"><span class="ic"><svg width="16" height="12" viewBox="0 0 16 12"><rect width="16" height="12" rx="1.5" fill="#1b8fe3"/><path d="M1 1l7 6 7-6" stroke="#fff" stroke-width="1.5" fill="none"/></svg></span><span>info@steadyharbordetailing.com</span></div>

<h3 class="block-title" style="left:782px;top:3230px">SOCIAL MEDIA</h3>
<div class="socials"><span></span><span></span><span></span><span></span></div>

<div class="footer-line"></div>
<p class="copyright">Copyright © 2018, Steady Harbor Detailing. All rights reserved.</p>
<svg class="to-top" width="32" height="18" viewBox="0 0 32 18"><path d="M2 16L16 3l14 13" stroke="#aaa" stroke-width="3" fill="none"/></svg>

</body>
</html>
```